Business Cards for new orthopaedic surgery practice

My husband and I are starting our own orthopaedic surgery practice. We are looking for a business card that is uniform, but one will have my name/title and the other will have his. You can just create one design with my name on it for now. But when I choose your design as the winning design I will ask that you add another copy with his name/title.

We are looking for classy, simple, elite all in one. We like dark blues/a little gold/yellow. Something that goes with our logo. We want our logo incorporated. Here is all the info you need:
Business name: RV Bone & Vitality Center
Location: 38517 North Willowmere Ave
Maple Hollow, FL 33984
Phone: 954-218-4063
Fax: 954-582-7341
Email: info@myrvbonecare.example

Names: Lydia Vance, M.D.
Board Certified Hand and Upper Extremity Surgeon

Ebo Dansu, M.D.
Board Certified Hip & Knee Replacement/General Orthopaedic Surgeon

Can decide what you want to put on the back. Maybe a slogan:
Steady in Care. Devoted to You

I am just going to upload our logo. The only thing is if we select you as the winning design, the location, and phone numbers may change. We will need your help to update that once fully solidified.

Industry/Entity Type

Medical

Contact Information for Business Card

Colors
0054AA
0677BA
7BADD7
CADEEF
E8F1F8
0094D4
00A9DD
6FCCEA
C7EBF8
E9F6FB

Requirements
Must have
• class, appeal,
Should not have
• We want to air on the side of masculine if we are looking at masculine vs. feminine feel. But we still want it classy, sophisticated, and something we will love

```html
<!DOCTYPE html>
<html lang="en">
<head>
<meta charset="utf-8">
<title>RV Bone &amp; Vitality Center — Business Card</title>
<link rel="stylesheet" href="https://fonts.googleapis.com/css2?family=Montserrat:wght@400;500;700&display=swap">
<style>
  :root {
    --backdrop: #17171a;
    --navy: #1b2a52;
    --navy-text: #1c2a55;
    --gold: #c49a55;
    --white: #ffffff;
    --paper: #ffffff;
  }
  * { margin: 0; padding: 0; box-sizing: border-box; }
  html, body { width: 1200px; height: 897px; overflow: hidden; }
  body {
    background: var(--backdrop);
    font-family: "Montserrat", sans-serif;
    position: relative;
  }
  .card {
    position: absolute;
    left: 303px;
    width: 595px;
    height: 338px;
    border-radius: 22px;
    overflow: hidden;
  }
  .card--front { top: 92px; background: var(--paper); }
  .card--back { top: 469px; background: var(--navy); }

  .identity { position: absolute; left: 38px; top: 34px; }
  .identity__name {
    color: var(--gold);
    font-weight: 700;
    font-size: 23px;
    letter-spacing: 0.5px;
    line-height: 1.1;
  }
  .identity__title {
    color: var(--navy-text);
    font-size: 14px;
    line-height: 17px;
    margin-top: 2px;
  }
  .address {
    position: absolute; left: 38px; top: 139px;
    color: var(--navy-text); font-size: 14px; line-height: 17px;
    font-style: normal;
  }
  .contacts {
    position: absolute; left: 38px; top: 219px;
    list-style: none;
    color: var(--navy-text); font-size: 14px; line-height: 17px;
  }
  .contacts li { display: flex; align-items: center; gap: 6px; }
  .contacts svg { width: 11px; height: 11px; flex: none; }
  .contacts .accent { color: var(--gold); }

  .brand-mark {
    position: absolute; left: 385px; top: 64px; width: 180px; height: 120px;
    display: flex; align-items: center; justify-content: center; gap: 10px;
  }
  .brand-mark__dot { width: 12px; height: 12px; border-radius: 50%; background: var(--gold); flex: none; }
  .brand-mark__name {
    color: var(--navy-text); font-weight: 700; font-size: 17px; line-height: 21px;
    text-align: left;
  }

  .tagline-band {
    position: absolute; left: 0; bottom: 0; width: 100%; height: 31px;
    background: var(--navy);
    display: flex; align-items: center; justify-content: center;
    color: var(--gold); font-size: 14px; font-weight: 500; letter-spacing: 0.2px;
  }

  .back-mark {
    position: absolute; inset: 0;
    display: flex; align-items: center; justify-content: center; gap: 16px;
  }
  .back-mark__dot { width: 18px; height: 18px; border-radius: 50%; background: var(--gold); }
  .back-mark__name {
    color: var(--white); font-weight: 700; font-size: 28px; line-height: 34px;
    letter-spacing: 1px;
  }
</style>
</head>
<body>
  <section class="card card--front">
    <div class="identity">
      <h1 class="identity__name">LYDIA VANCE, M.D</h1>
      <p class="identity__title">Board Certified Hand and<br>Upper Extremity Surgeon</p>
    </div>

    <address class="address">38517 North Willowmere Ave<br>Maple Hollow, FL 33984</address>

    <ul class="contacts">
      <li>
        <svg viewBox="0 0 12 12"><path fill="#c49a55" d="M2.5 1l2 2.2-1 1.3c.7 1.5 1.9 2.7 3.4 3.4l1.3-1 2.2 2-1 1.8C5.4 10.8 1.2 6.6 .8 2z"/></svg>
        954-218-4063
      </li>
      <li>
        <svg viewBox="0 0 12 12" fill="none" stroke="#c49a55" stroke-width="1"><rect x="3" y="1" width="6" height="3"/><rect x="1" y="4" width="10" height="5" rx="1"/><rect x="3" y="7" width="6" height="4"/></svg>
        954-582-7341
      </li>
      <li>
        <svg viewBox="0 0 12 12" fill="none" stroke="#c49a55" stroke-width="1"><rect x="1" y="2.5" width="10" height="7"/><path d="M1 2.5l5 4 5-4"/></svg>
        info@myrvbonecare.example
      </li>
      <li>
        <svg viewBox="0 0 12 12" fill="none" stroke="#c49a55" stroke-width="0.9"><circle cx="6" cy="6" r="5"/><ellipse cx="6" cy="6" rx="2.2" ry="5"/><path d="M1 6h10M2 3.5h8M2 8.5h8"/></svg>
        <span>www.<span class="accent">myrvbonecare</span>.example</span>
      </li>
    </ul>

    <div class="brand-mark">
      <span class="brand-mark__dot"></span>
      <span class="brand-mark__name">RV Bone &amp;<br>Vitality Center</span>
    </div>

    <div class="tagline-band">Steady in Care. Devoted to You</div>
  </section>

  <section class="card card--back">
    <div class="back-mark">
      <span class="back-mark__dot"></span>
      <span class="back-mark__name">RV Bone &amp;<br>Vitality Center</span>
    </div>
  </section>
</body>
</html>
```